Logo and Card design for KRV Home Solutions LLC

I need an edgier logo and business card designs. Current logo attached. I like the colors below. I would like the logo to incorporate a home in the design.
Title = Principal-Acquisitions
Email:KRVHOMESOLUTIONS@fernmail.example
555-214-0937
facebook
IG
2 sided business card with the front being contact info a slogan about selling a home fast. The back incorporating What we do. Buy houses, land, or commercial property as is. We find solutions to make the process of selling simple and fair.

Target Market(s)

Motivated house sellers.

Industry/Entity Type

Business

Contact Information for Business Card

Who we are: We are a Faith based Real Estate Investment Company. We pay cash for homes in any condition and can close quick. Whatever the reason you need to sell fast, we can help. We believe in creating win-win solutions to help you in your time of need. We care! We can help!

Logo Text

KRV Home Solutions LLC

Font styles to use
Sans Serif

Colors
33a6d7
0355a3
85abd2
cee9f5
9d9d9d
b2b2b2
ffffff

Requirements
Must have
• Old logo attached. I want something edgier.
• Company name, phone number, description on the back of what we can do. Pay all cash. Buy in as is condition. No fees,Commisions or closing costs.Close quick. No hassles with solutions to meet your unique situation.
• Call today for an offer within 24 hours.

```html
<!DOCTYPE html>
<html lang="en">
<head>
<meta charset="utf-8">
<title>KRV Home Solutions – Business Card</title>
<link href="https://fonts.googleapis.com/css2?family=Roboto:wght@400;500;700&family=Roboto+Condensed:wght@400;700&display=swap" rel="stylesheet">
<style>
  :root {
    --navy: #1d3466;
    --slate: #505a66;
    --grey-text: #5a5f66;
    --rule: #b2b2b2;
    --white: #ffffff;
    --page: #e9e6e2;
    --photo-sky: #e4edf3;
    --photo-mid: #c9d7e0;
    --photo-low: #b3c4cf;
  }
  * { box-sizing: border-box; margin: 0; padding: 0; }
  html, body { width: 1200px; height: 960px; overflow: hidden; }
  body {
    background: var(--page);
    position: relative;
    font-family: "Roboto", Arial, sans-serif;
  }
  .card {
    position: absolute;
    width: 600px;
    height: 343px;
    box-shadow: 0 3px 6px rgba(0,0,0,.35);
    overflow: hidden;
  }
  .card--front { left: 314px; top: 113px; background: var(--white); }
  .card--back { left: 312px; top: 472px; background: var(--navy); color: var(--white); text-align: center; }

  .front__photo {
    position: absolute; left: 0; top: 0; width: 600px; height: 258px;
    background: linear-gradient(180deg, var(--photo-sky) 0%, #eef2f4 45%, var(--photo-mid) 78%, var(--photo-low) 100%);
  }
  .front__rule {
    position: absolute; left: 0; top: 258px; width: 600px; height: 3px; background: var(--rule);
  }
  .front__band {
    position: absolute; left: 0; top: 261px; width: 600px; height: 82px;
    background: var(--navy); color: var(--white);
    font-family: "Roboto Condensed", Arial, sans-serif;
    font-size: 14px; line-height: 18.5px; text-align: center;
    padding-top: 13px;
  }

  .brand {
    display: flex; align-items: center; gap: 10px;
    font-family: "Roboto", Arial, sans-serif; font-weight: 700;
  }
  .brand__mark { flex: none; }
  .brand__name { display: block; text-align: left; }
  .brand__line { display: block; }

  .front .brand {
    position: absolute; left: 68px; top: 106px; width: 190px;
    color: var(--navy); font-size: 28px; line-height: 32px;
  }
  .front .brand__mark { width: 16px; height: 16px; background: var(--navy); }

  .front__divider {
    position: absolute; left: 271px; top: 70px; width: 1px; height: 120px; background: var(--rule);
  }
  .contact { position: absolute; left: 293px; top: 76px; }
  .contact__name {
    font-family: "Roboto Condensed", Arial, sans-serif; font-weight: 700;
    font-size: 25px; color: var(--navy); line-height: 28px;
  }
  .contact__title {
    font-family: "Roboto Condensed", Arial, sans-serif; font-size: 17px;
    color: var(--grey-text); line-height: 22px;
  }
  .contact__list { list-style: none; margin-top: 6px; }
  .contact__item {
    display: flex; align-items: center; gap: 9px;
    font-size: 14.5px; color: var(--slate); line-height: 19px;
  }
  .contact__item svg { width: 13px; height: 13px; flex: none; fill: var(--navy); }

  .back .brand {
    justify-content: center; color: var(--white);
    font-size: 32px; line-height: 35px; margin-top: 78px;
  }
  .back .brand__mark { width: 18px; height: 18px; background: var(--white); }
  .back__section { margin-top: 18px; }
  .back__section + .back__section { margin-top: 10px; }
  .back__heading { font-size: 15px; font-weight: 500; line-height: 20px; }
  .back__text { font-size: 14.5px; line-height: 18px; padding: 0 44px; }
</style>
</head>
<body>

<section class="card card--front front">
  <div class="front__photo" role="img" aria-label="Soft faded photo of a homeowner in front of a house with trees"></div>
  <div class="brand">
    <span class="brand__mark"></span>
    <span class="brand__name"><span class="brand__line">KRV HOME</span><span class="brand__line">SOLUTIONS</span></span>
  </div>
  <div class="front__divider"></div>
  <div class="contact">
    <div class="contact__name">EVAN MARLOW</div>
    <div class="contact__title">Principal-Acquisitions</div>
    <ul class="contact__list">
      <li class="contact__item">
        <svg viewBox="0 0 24 24" aria-hidden="true"><path d="M6.6 10.8a15.1 15.1 0 0 0 6.6 6.6l2.2-2.2a1 1 0 0 1 1-.25 11.4 11.4 0 0 0 3.6.57 1 1 0 0 1 1 1V20a1 1 0 0 1-1 1A17 17 0 0 1 3 4a1 1 0 0 1 1-1h3.5a1 1 0 0 1 1 1c0 1.25.2 2.45.57 3.57a1 1 0 0 1-.25 1z"/></svg>
        555-214-0937
      </li>
      <li class="contact__item">
        <svg viewBox="0 0 24 24" aria-hidden="true"><path d="M2 5h20v14H2z"/><path d="M2 5h20v1.8l-10 6.7L2 6.8z" fill="#fff" opacity=".9"/></svg>
        KRVHOMESOLUTIONS@fernmail.example
      </li>
      <li class="contact__item">
        <svg viewBox="0 0 24 24" aria-hidden="true"><circle cx="12" cy="12" r="10"/><path d="M12 2v20M2 12h20" stroke="#fff" stroke-width="1.6" fill="none"/></svg>
        KRVHOMESOLUTIONS.example
      </li>
    </ul>
  </div>
  <div class="front__rule"></div>
  <div class="front__band">
    Pay all cash. Buy in as is condition.• No fees,Commisions or closing costs.<br>
    Close quick. No hassles with solutions to meet your unique situation.<br>
    Call today for an offer within 24 hours.
  </div>
</section>

<section class="card card--back back">
  <div class="brand">
    <span class="brand__mark"></span>
    <span class="brand__name"><span class="brand__line">KRV HOME</span><span class="brand__line">SOLUTIONS</span></span>
  </div>
  <div class="back__section">
    <h2 class="back__heading">WHO WE ARE</h2>
    <p class="back__text">We are a Faith based Real Estate Investment Company. We pay cash for homes in any condition and can close quick. Whatever the reason you need to sell fast, we can help. We believe in creating win-win solutions to help</p>
  </div>
  <div class="back__section">
    <h2 class="back__heading">WHAT WE DO</h2>
    <p class="back__text">Buy houses, land, or commercial property as is.<br>We find solutions to make the process of selling simple and fair.</p>
  </div>
</section>

</body>
</html>
```